Corporate Business Card

Very professional, Modern, Not to busy, include phone address email, website
(253) 617-4930, 18761 52nd Avenue S, Kent, WA 98047, martin@plumlinegroup.com, varkoworks.com

Target Market(s)

Manufacturing

Industry/Entity Type

Aero, machining, manufacturing, Off road racing

Contact Information for Business Card

Phone, address email, website

```html
<!DOCTYPE html>
<html lang="en">
<head>
<meta charset="utf-8">
<title>Varko Works – Business Card</title>
<link rel="stylesheet" href="https://fonts.googleapis.com/css2?family=Lato:wght@400;900&family=Orbitron:wght@900&display=swap">
<style>
  :root {
    --backdrop: #1d1d1f;
    --navy: #15336f;
    --red: #d2232a;
    --paper: #ffffff;
    --ink: #3f3f44;
  }
  * { box-sizing: border-box; margin: 0; padding: 0; }
  html, body { width: 1200px; height: 1122px; overflow: hidden; }
  body {
    background: var(--backdrop);
    font-family: "Lato", sans-serif;
    position: relative;
  }
  .card {
    position: absolute;
    left: 180px;
    width: 840px;
    height: 480px;
    overflow: hidden;
    box-shadow: 0 14px 30px rgba(0,0,0,.5);
  }
  /* Back of card */
  .card-back { top: 50px; background: var(--navy); }
  .back-brand {
    position: absolute;
    left: 0; right: 0; top: 170px;
    text-align: center;
    color: var(--paper);
    font-weight: 900;
    font-size: 68px;
    letter-spacing: 1px;
    line-height: 1;
  }
  .back-brand .brand-mark {
    display: inline-block;
    width: 30px; height: 30px;
    background: var(--paper);
    margin-right: 18px;
    vertical-align: 8px;
  }
  .back-rule {
    position: absolute;
    left: 200px; top: 272px;
    width: 440px; height: 2px;
    background: var(--paper);
  }

  /* Front of card */
  .card-front { top: 590px; background: var(--paper); }
  .front-brand {
    position: absolute;
    left: 70px; top: 48px;
    color: var(--navy);
    font-weight: 900;
    font-size: 52px;
    line-height: 1;
  }
  .front-brand .brand-mark {
    display: inline-block;
    width: 22px; height: 22px;
    background: var(--navy);
    margin-right: 14px;
    vertical-align: 6px;
  }
  .front-rule {
    position: absolute;
    left: 60px; top: 118px;
    width: 340px; height: 2px;
    background: var(--navy);
  }
  .name-band {
    position: absolute;
    left: 0; top: 148px;
    width: 480px; height: 118px;
  }
  .name-block {
    position: absolute;
    left: 40px; top: 172px;
    width: 400px;
    color: var(--paper);
  }
  .person-name {
    font-family: "Orbitron", sans-serif;
    font-weight: 900;
    font-size: 25px;
    letter-spacing: 1.5px;
    line-height: 1.2;
    white-space: nowrap;
  }
  .person-title {
    font-size: 21px;
    margin-top: 8px;
    letter-spacing: .5px;
  }
  .accent-line {
    position: absolute;
    left: 0; top: 0;
    width: 840px; height: 480px;
  }
  .contacts {
    position: absolute;
    left: 40px; top: 292px;
    list-style: none;
    color: var(--ink);
    font-size: 20px;
  }
  .contacts li {
    display: flex;
    align-items: center;
    gap: 12px;
    height: 30px;
  }
  .contacts svg { width: 16px; height: 16px; flex: none; }
  .address {
    position: absolute;
    right: 108px; top: 372px;
    text-align: right;
    color: var(--ink);
    font-size: 20px;
    font-style: normal;
    line-height: 1.35;
  }
</style>
</head>
<body>

  <section class="card card-back" aria-label="Card back">
    <div class="back-brand"><span class="brand-mark"></span>Varko Works</div>
    <div class="back-rule"></div>
  </section>

  <section class="card card-front" aria-label="Card front">
    <div class="front-brand"><span class="brand-mark"></span>Varko Works</div>
    <div class="front-rule"></div>

    <svg class="name-band" viewBox="0 0 480 118" aria-hidden="true">
      <polygon points="0,0 462,0 470,118 0,118" fill="var(--navy)"/>
    </svg>
    <svg class="accent-line" viewBox="0 0 840 480" aria-hidden="true">
      <polyline points="482,148 490,272 736,272" fill="none" stroke="var(--red)" stroke-width="4"/>
    </svg>

    <div class="name-block">
      <div class="person-name">DANIEL PRESCOTT</div>
      <div class="person-title">Managing Director</div>
    </div>

    <ul class="contacts">
      <li>
        <svg viewBox="0 0 16 16" aria-hidden="true"><path fill="var(--red)" d="M3.6 1.2l2.2 2.6-1.3 1.6c.9 2 2.3 3.5 4.2 4.4l1.6-1.3 2.6 2.2-1.2 2.4C6.3 12.8 2.9 9.4 1.2 4.4z"/></svg>
        (253) 617-4930
      </li>
      <li>
        <svg viewBox="0 0 16 16" aria-hidden="true"><rect x="1" y="3" width="14" height="10" fill="var(--red)"/><polyline points="1,3 8,9 15,3" fill="none" stroke="#fff" stroke-width="1.4"/></svg>
        martin@plumlinegroup.com
      </li>
      <li>
        <svg viewBox="0 0 16 16" aria-hidden="true"><circle cx="8" cy="8" r="7" fill="var(--red)"/><path d="M1.5 8h13M8 1c2.5 2.5 2.5 11.5 0 14M8 1c-2.5 2.5-2.5 11.5 0 14" fill="none" stroke="#fff" stroke-width="1"/></svg>
        www.varkoworks.com
      </li>
    </ul>

    <address class="address">
      18761 52nd Avenue S<br>
      Kent, WA 98047
    </address>
  </section>

</body>
</html>
```